Upstart Retirement Planning Firm needs help with business card design

Harborview Nest Advisors, LLC is looking for help with business card design. We give advice on investments, insurance, and other financial matters related to retirement. There are some required disclosures that we will provide but mostly we are looking for a professional, classy business card that reflects the theme we have chosen. We have a logo that is attached but we would like to add a phrase; "Turning Your Earned Income Into Retirement Income"

Doubled sided only so that we can add the required disclosures (needed for our industry) on the back of the card. We will provide the exact words for this in 1-2 days.

Target Market(s)

Retirees and Pre-retirees. Professionals 50+ years old

Industry/Entity Type

Financial Planning

Contact Information for Business Card

We currently have two people who will need separate cards so we'd like to have a template so that we can add names for new cards in the future.

For the first run, please show the following information.

Gregor Pelham, MBA, ChFC®, CLU®
Financial Advisor, Registered Representative
gpelham@harborviewnest.example
Phone: (555) 318-2946
Toll Free Fax: (800) 555-0193

Address is
2187 Meadowlark Ridge Rd.
Suite K418
Virginia Beach, VA 23999

Colors
3277b5

Requirements
Must have
• Logo, contact info, small phase to describe business (in description), required legal disclosures on back of the card as follows (in small font)
• Gregor Pelham is a registered representative of and offers securities through Brightmoor Capital Brokerage Corporation, Member FNQX. Brightmoor Capital Brokerage Corporation is a member of the Brightmoor Capital Alliance which is the marketing name for Brightmoor Holding Corporation and its affiliates.
Nice to have
• Rounded edges, raised letters
Should not have
• any colors that aren't in the logo (other than black for font)

```html
<!DOCTYPE html>
<html lang="en">
<head>
<meta charset="utf-8">
<title>Harborview Nest Advisors — Business Card</title>
<link rel="stylesheet" href="https://fonts.googleapis.com/css2?family=Arimo:wght@400&family=Tenor+Sans&display=swap">
<style>
  :root {
    --backdrop: #e9e6e1;
    --card: #ffffff;
    --brand-blue: #1f4f9c;
    --brand-grey: #8d9196;
    --ink: #1b1b1b;
    --ink-soft: #3a3a3a;
    --tagline: #55585c;
    --rule: #6e6e6e;
  }
  * { margin: 0; padding: 0; box-sizing: border-box; }
  html, body {
    width: 1200px;
    height: 1000px;
    overflow: hidden;
    background: var(--backdrop);
  }
  .stage {
    position: relative;
    width: 1200px;
    height: 1000px;
  }
  .business-card {
    position: absolute;
    left: 293px;
    top: 322px;
    width: 612px;
    height: 358px;
    background: var(--card);
    border-radius: 16px;
    box-shadow: 0 3px 8px rgba(0,0,0,0.18);
    font-family: "Arimo", Arial, sans-serif;
    color: var(--ink);
    overflow: hidden;
  }
  .brand {
    position: absolute;
    left: 21px;
    top: 40px;
    width: 298px;
    display: flex;
    align-items: center;
    gap: 14px;
  }
  .brand-mark {
    flex: none;
    width: 46px;
    height: 46px;
    border-radius: 50%;
    background: var(--brand-grey);
  }
  .brand-name {
    font-family: "Arimo", Arial, sans-serif;
    font-weight: 400;
    font-size: 26px;
    line-height: 1.15;
    color: var(--brand-blue);
    letter-spacing: 0.5px;
  }
  .tagline {
    position: absolute;
    left: 346px;
    top: 74px;
    width: 254px;
    text-align: center;
    font-family: "Tenor Sans", "Trebuchet MS", sans-serif;
    font-variant: small-caps;
    font-size: 17px;
    line-height: 23px;
    color: var(--tagline);
    letter-spacing: 0.2px;
  }
  .advisor {
    position: absolute;
    right: 360px;
    top: 220px;
    text-align: right;
  }
  .advisor-name {
    font-size: 17px;
    line-height: 22px;
    letter-spacing: 0.3px;
    color: var(--ink);
    text-transform: uppercase;
  }
  .advisor-role {
    font-size: 15px;
    line-height: 19.5px;
    color: var(--ink-soft);
  }
  .advisor-role:first-of-type { margin-top: 3px; }
  .divider {
    position: absolute;
    left: 306px;
    top: 215px;
    width: 1px;
    height: 126px;
    background: var(--rule);
  }
  .contact {
    position: absolute;
    left: 338px;
    top: 222px;
    width: 262px;
    font-style: normal;
    font-size: 15px;
    line-height: 19.6px;
    color: var(--ink-soft);
    white-space: nowrap;
  }
  .contact .email {
    margin-top: 2px;
    font-size: 13.5px;
    letter-spacing: -0.1px;
  }
</style>
</head>
<body>
<main class="stage">
  <article class="business-card">
    <div class="brand">
      <span class="brand-mark" aria-hidden="true"></span>
      <span class="brand-name">Harborview Nest Advisors, LLC</span>
    </div>

    <p class="tagline">Turning Your Earned Income<br>Into Retirement Income</p>

    <div class="advisor">
      <p class="advisor-name">Gregor Pelham</p>
      <p class="advisor-role">MBA, ChFC®, CLU®</p>
      <p class="advisor-role">Financial Advisor</p>
      <p class="advisor-role">Registered Representative</p>
    </div>

    <span class="divider" aria-hidden="true"></span>

    <address class="contact">
      <p>2187 Meadowlark Ridge Rd.</p>
      <p>Suite K418, Virginia Beach</p>
      <p>VA 23999</p>
      <p>Phone: (555) 318-2946</p>
      <p>Toll Free Fax: (800) 555-0193</p>
      <p class="email">Email: gpelham@harborviewnest.example</p>
    </address>
  </article>
</main>
</body>
</html>
```